Interior Design/ New Construction interior finishes

Interior Design Website

Target Market(s)

Home builders, New Construction, Renovations, Public

Industry/Entity Type

Construction

Coding

Coded - Design and coding required

Number of Pages Required

1 page

Font styles to use
Sans Serif

Colors

Designer to choose colors to be used in the design.

Requirements
Must have
• Section to upload pictures of projects
• Simple and modern design
• Designer 1 details about myself
• Logo
• Upload section for photos for future jobs
Nice to have
• Sections they can click on to see certain rooms in a house
• Decorating, floral arrangements, holiday decorating.
• I have lots of before and after as well. Maybe a section for those.

```html
<!DOCTYPE html>
<html lang="en">
<head>
<meta charset="utf-8">
<title>KV Interiors</title>
<link rel="stylesheet" href="https://fonts.googleapis.com/css2?family=Mulish:wght@400;600;700&display=swap">
<style>
:root{
  --ink:#111111;
  --text:#333333;
  --muted:#555555;
  --line:#8a8a8a;
  --paper:#ffffff;
  --band:#f0f0f0;
  --footer:#2b2b2b;
  --footer-text:#bdbdbd;
  --card:#000000;
}
*{box-sizing:border-box;margin:0;padding:0}
html,body{width:1200px;height:2192px;overflow:hidden;background:var(--paper)}
body{position:relative;font-family:"Mulish",Arial,sans-serif;color:var(--text)}
.abs{position:absolute}

/* header */
.brand-mark{left:188px;top:25px;width:82px;height:82px;border:3px solid var(--ink);border-radius:50%}
.brand-name{left:133px;top:108px;width:200px;font-size:29px;letter-spacing:4px;color:var(--ink);white-space:nowrap}
.header-phone{right:133px;top:50px;font-size:24px;color:var(--ink);display:flex;align-items:center;gap:8px}
.main-nav{right:133px;top:117px;display:flex;gap:37px;font-size:17px;color:var(--ink)}

/* hero */
.hero{left:0;top:156px;width:1200px;height:458px;background:linear-gradient(90deg,#e9ebec 0%,#d9dcdd 35%,#cfd3d5 60%,#bfc3c6 80%,#9aa0a4 100%)}
.hero-arrow{top:373px;width:28px;height:26px;background:#222;display:flex;align-items:center;justify-content:center}
.hero-arrow.prev{left:0}
.hero-arrow.next{right:0}

/* service cards */
.service{top:655px;width:303px;height:304px;background:var(--card)}
.service .photo{position:absolute;left:12px;top:13px;right:12px;height:225px;border:2px solid #fff}
.service .label{position:absolute;left:0;right:0;top:252px;text-align:center;color:#fff;font-size:24px}

.rule{left:133px;width:934px;height:1px;background:var(--line)}

/* welcome */
.welcome-title{left:0;width:1200px;top:1050px;text-align:center;font-size:32px;color:var(--ink);font-weight:400}
.welcome-text{left:137px;width:926px;top:1103px;text-align:center;font-size:16.6px;line-height:26px;color:var(--muted)}
.btn-contact{left:528px;top:1225px;width:143px;height:47px;border:2px solid var(--ink);display:flex;align-items:center;justify-content:center;font-weight:700;font-size:16px;color:var(--ink)}

/* works */
.works-title{left:0;width:1200px;top:1421px;text-align:center;font-size:32px;color:var(--ink);font-weight:400}
.work{top:1481px;width:297px;height:343px;background:var(--card);padding:7px}
.work .shot{position:relative;height:161px}
.work .shot + .shot{margin-top:7px}
.work .tag{position:absolute;left:0;bottom:4px;background:#fff;color:var(--ink);font-size:13px;padding:4px 10px 4px 9px}
.works-arrow{top:1636px}

/* contact */
.contact-band{left:0;top:1905px;width:1200px;height:191px;background:var(--band)}
.contact-title{left:0;width:1200px;top:1942px;text-align:center;font-size:32px;color:var(--ink);font-weight:400}
.contact-address{left:0;width:1200px;top:1991px;display:flex;justify-content:center;align-items:center;gap:8px;font-size:16.5px;color:var(--muted)}
.contact-lines{left:0;width:1200px;top:2021px;display:flex;justify-content:center;gap:30px;font-size:21px;color:var(--ink)}
.contact-lines span{display:flex;align-items:center;gap:10px}

/* footer */
.site-footer{left:0;top:2096px;width:1200px;height:96px;background:var(--footer)}
.footer-links{left:133px;top:2122px;font-size:11px;color:var(--footer-text);word-spacing:2px}
.footer-copy{left:133px;top:2150px;font-size:10.5px;color:var(--footer-text)}
.social{top:2127px;width:32px;height:32px;border-radius:50%;background:#777}
</style>
</head>
<body>

<header>
  <div class="abs brand-mark"></div>
  <div class="abs brand-name">KV Interiors</div>
  <div class="abs header-phone">
    <svg width="18" height="18" viewBox="0 0 24 24"><path fill="#111" d="M6.6 10.8a15.1 15.1 0 0 0 6.6 6.6l2.2-2.2c.3-.3.7-.4 1-.2 1.1.4 2.3.6 3.6.6.6 0 1 .4 1 1V20c0 .6-.4 1-1 1C10.6 21 3 13.4 3 4c0-.6.4-1 1-1h3.5c.6 0 1 .4 1 1 0 1.3.2 2.5.6 3.6.1.3 0 .7-.2 1z"/></svg>
    555 014 2278
  </div>
  <nav class="abs main-nav">
    <span>Home</span><span>About Us</span><span>Services</span><span>Gallery</span><span>Contact Us</span>
  </nav>
</header>

<section class="abs hero" role="img" aria-label="Bright white bathroom with glass shower, walk-in closet and dark stone vanity"></section>
<div class="abs hero-arrow prev"><svg width="14" height="12" viewBox="0 0 14 12"><path d="M13 6H2M6 1 1 6l5 5" stroke="#fff" stroke-width="2.4" fill="none"/></svg></div>
<div class="abs hero-arrow next"><svg width="14" height="12" viewBox="0 0 14 12"><path d="M1 6h11M8 1l5 5-5 5" stroke="#fff" stroke-width="2.4" fill="none"/></svg></div>

<section>
  <div class="abs service" style="left:133px">
    <div class="photo" role="img" aria-label="Dining room with crystal chandeliers and stone wall" style="background:linear-gradient(160deg,#6e7270,#4a3f35 60%,#2d241d)"></div>
    <div class="label">Feature Decorating</div>
  </div>
  <div class="abs service" style="left:449px">
    <div class="photo" role="img" aria-label="Living room table with purple flower arrangement" style="background:linear-gradient(160deg,#c9c8c3,#a9a39a 55%,#7c6f61)"></div>
    <div class="label">Floral Arrangements</div>
  </div>
  <div class="abs service" style="left:764px">
    <div class="photo" role="img" aria-label="Children's room with loft staircase and patterned rug" style="background:linear-gradient(160deg,#8e97a8,#b7a999 55%,#8a6a4f)"></div>
    <div class="label">Holiday Decorating</div>
  </div>
</section>

<div class="abs rule" style="top:979px"></div>

<section>
  <h1 class="abs welcome-title">Welcome to KV Interiors</h1>
  <p class="abs welcome-text">Fusce nec leo ac urna pulvinar auctor. Mauris bibendum fringilla velit. Nulla in lorem at massa pellentesque posuere. Nulla tristique posuere molestie. Aliquam erat volutpat. Etiam quis aliquet risus. Duis ornare erat eget magna dapibus, in accumsan quam pharetra. Nam tempus, quam in bibendum vulputate, sapien dolor viverra nisl, vitae euismod elit turpis et nulla. Aliquam erat volutpat. Pellentesque blandit lacus eget nunc faucibus, et tincidunt eros viverra.</p>
  <div class="abs btn-contact">CONTACT US</div>
</section>

<div class="abs rule" style="top:1351px"></div>

<section>
  <h2 class="abs works-title">Our Works</h2>
  <svg class="abs works-arrow" style="left:46px" width="16" height="30" viewBox="0 0 16 30"><path d="M14 2 2 15l12 13" stroke="#888" stroke-width="2" fill="none"/></svg>
  <svg class="abs works-arrow" style="left:1137px" width="16" height="30" viewBox="0 0 16 30"><path d="M2 2l12 13L2 28" stroke="#888" stroke-width="2" fill="none"/></svg>

  <div class="abs work" style="left:133px">
    <div class="shot" role="img" aria-label="Bathroom before renovation" style="background:linear-gradient(160deg,#d8d6d2,#a9a49c 60%,#8a7c6d)"><span class="tag">Before</span></div>
    <div class="shot" role="img" aria-label="Bathroom after renovation" style="background:linear-gradient(160deg,#dcdad6,#b3aca2 60%,#7f6d5b)"><span class="tag">After</span></div>
  </div>
  <div class="abs work" style="left:452px">
    <div class="shot" role="img" aria-label="Living room before renovation" style="background:linear-gradient(160deg,#6b5a48,#3a2f26 60%,#2a2019)"><span class="tag">Before</span></div>
    <div class="shot" role="img" aria-label="Living room after renovation" style="background:linear-gradient(160deg,#5d4a38,#3b2e24 60%,#6d5440)"><span class="tag">After</span></div>
  </div>
  <div class="abs work" style="left:770px">
    <div class="shot" role="img" aria-label="Kitchen before renovation" style="background:linear-gradient(160deg,#f0f0ee,#c9c6c0 60%,#8d8276)"><span class="tag">Before</span></div>
    <div class="shot" role="img" aria-label="Kitchen after renovation" style="background:linear-gradient(160deg,#eeeeec,#c4c1bb 60%,#857a6e)"><span class="tag">After</span></div>
  </div>
</section>

<section>
  <div class="abs contact-band"></div>
  <h2 class="abs contact-title">Contact Us</h2>
  <div class="abs contact-address">
    <svg width="9" height="13" viewBox="0 0 10 14"><path fill="#333" d="M5 0a5 5 0 0 0-5 5c0 3.8 5 9 5 9s5-5.2 5-9a5 5 0 0 0-5-5zm0 7a2 2 0 1 1 0-4 2 2 0 0 1 0 4z"/></svg>
    24 Building name, Street name, City Zipcode
  </div>
  <div class="abs contact-lines">
    <span><svg width="17" height="17" viewBox="0 0 24 24"><path fill="#111" d="M6.6 10.8a15.1 15.1 0 0 0 6.6 6.6l2.2-2.2c.3-.3.7-.4 1-.2 1.1.4 2.3.6 3.6.6.6 0 1 .4 1 1V20c0 .6-.4 1-1 1C10.6 21 3 13.4 3 4c0-.6.4-1 1-1h3.5c.6 0 1 .4 1 1 0 1.3.2 2.5.6 3.6.1.3 0 .7-.2 1z"/></svg>555 014 3390</span>
    <span><svg width="19" height="15" viewBox="0 0 20 15"><path fill="#111" d="M0 0h20v2l-10 6L0 2zM0 4l10 6 10-6v11H0z"/></svg>hello@kvinteriors.com</span>
  </div>
</section>

<footer>
  <div class="abs site-footer"></div>
  <div class="abs footer-links">Home &nbsp;| &nbsp;About Us &nbsp;| &nbsp;Services &nbsp;| &nbsp;Gallery &nbsp;| &nbsp;Contact Us</div>
  <div class="abs footer-copy">Copyright &copy; 2018 KV Interiors. All rights reserved.</div>
  <div class="abs social" style="left:991px"></div>
  <div class="abs social" style="left:1035px"></div>
</footer>

</body>
</html>
```